New Business Card Design Project

Need a design that will create an impact / strong impression towards our clients for our business. We are in the lighting business and we do lighting retrofits for large commercial to industrial clientele.

Target Market(s)

Lighting Industry

Industry/Entity Type

Business

Font styles to use
Other font styles liked:
• we would like to use the font on our logo, not sure what it is though..

Requirements
Must have
• Our logo.
Nice to have
• We are open to suggestions that have to do with lighting.

```html
<!DOCTYPE html>
<html lang="en">
<head>
<meta charset="utf-8">
<title>Kestrova Retrofit Group – Business Card</title>
<link href="https://fonts.googleapis.com/css2?family=Roboto:wght@400;500;700&display=swap" rel="stylesheet">
<style>
  :root{
    --page-bg:#e4e6e5;
    --card-top:#f1f3f2;
    --card-bottom:#d9dedb;
    --brand-dark:#123a1c;
    --green-light:#4fae4a;
    --green-mid:#2f8d35;
    --green-deep:#0f5a22;
    --green-darkest:#0a4219;
    --text-name:#cfe9b8;
    --text-light:#e6f2dc;
    --icon:#9fd98a;
  }
  *{margin:0;padding:0;box-sizing:border-box;}
  html,body{width:1200px;height:969px;overflow:hidden;}
  body{background:var(--page-bg);font-family:"Roboto",Arial,sans-serif;position:relative;}
  .business-card{
    position:absolute;left:100px;top:200px;width:1000px;height:569px;
    background:linear-gradient(180deg,var(--card-top),var(--card-bottom));
    border-radius:6px;overflow:hidden;
    box-shadow:0 10px 30px rgba(0,0,0,.18);
  }
  .card-bands{position:absolute;inset:0;width:100%;height:100%;}
  .brand{
    position:absolute;left:0;right:0;top:122px;
    display:flex;justify-content:center;align-items:center;gap:18px;
  }
  .brand-mark{width:26px;height:26px;background:var(--green-mid);}
  .brand-name{font-weight:700;font-size:46px;letter-spacing:1px;color:var(--brand-dark);}
  .holder{position:absolute;left:50px;top:390px;color:var(--text-light);}
  .holder-name{font-size:34px;font-weight:500;color:var(--text-name);letter-spacing:.5px;}
  .holder-title{font-size:26px;margin-top:6px;letter-spacing:.5px;}
  .holder-address{font-size:22px;margin-top:6px;line-height:1.35;}
  .contact-list{
    position:absolute;right:46px;top:400px;list-style:none;
    color:var(--text-light);font-size:23px;text-align:right;
  }
  .contact-list li{display:flex;justify-content:flex-end;align-items:center;gap:12px;height:34px;}
  .contact-list svg{width:20px;height:20px;flex:none;}
</style>
</head>
<body>
  <section class="business-card">
    <svg class="card-bands" viewBox="0 0 1000 569" preserveAspectRatio="none" aria-hidden="true">
      <defs>
        <linearGradient id="bandLeft" x1="0" y1="0" x2="0" y2="1">
          <stop offset="0" stop-color="#4fae4a"/>
          <stop offset="1" stop-color="#2f8d35"/>
        </linearGradient>
        <linearGradient id="bandRight" x1="0" y1="0" x2="1" y2="1">
          <stop offset="0" stop-color="#0f5a22"/>
          <stop offset="1" stop-color="#0a4219"/>
        </linearGradient>
      </defs>
      <polygon points="0,248 500,424 500,569 0,569" fill="url(#bandLeft)"/>
      <polygon points="500,424 1000,248 1000,569 500,569" fill="url(#bandRight)"/>
    </svg>

    <div class="brand">
      <span class="brand-mark"></span>
      <span class="brand-name">KESTROVA RETROFIT GROUP</span>
    </div>

    <div class="holder">
      <p class="holder-name">DANIEL HARLOW</p>
      <p class="holder-title">CEO/FOUNDER</p>
      <p class="holder-address">2140 Willowbend Road<br>Fairbanks, Alaska 99701</p>
    </div>

    <ul class="contact-list">
      <li>907 555 0142
        <svg viewBox="0 0 20 20"><path d="M5 2l3 4-2 2c1 2 3 4 5 5l2-2 4 3-2 3C9 17 3 11 2 5z" fill="var(--icon)"/></svg>
      </li>
      <li>907 555 0187
        <svg viewBox="0 0 20 20"><rect x="5" y="1" width="10" height="18" rx="2" fill="none" stroke="var(--icon)" stroke-width="2"/><circle cx="10" cy="15.5" r="1.2" fill="var(--icon)"/></svg>
      </li>
      <li>907 555 0163
        <svg viewBox="0 0 20 20"><rect x="5" y="2" width="10" height="5" fill="var(--icon)"/><rect x="2" y="8" width="16" height="7" rx="1" fill="var(--icon)"/><rect x="5" y="13" width="10" height="5" fill="var(--icon)"/></svg>
      </li>
      <li>daniel@example.com
        <svg viewBox="0 0 20 20"><rect x="2" y="4" width="16" height="12" rx="1" fill="var(--icon)"/><path d="M2 5l8 6 8-6" fill="none" stroke="var(--green-deep)" stroke-width="1.5"/></svg>
      </li>
    </ul>
  </section>
</body>
</html>
```